- Redesign our business card
- Logo remains unchanged
- Current business card attached

Target Market(s)

We are a property management company

Industry/Entity Type

Business

```html
<!DOCTYPE html>
<html lang="en">
<head>
<meta charset="utf-8">
<title>Harlow Property Group – Business Card</title>
<link rel="stylesheet" href="https://fonts.googleapis.com/css2?family=Source+Sans+3:wght@400&display=swap">
<style>
  :root {
    --page: #ffffff;
    --card: #f7f8fa;
    --frame: #e6e5dd;
    --mark-sand: #e0d1a9;
    --ink-grey: #6b6c70;
    --ink-slate: #8c95a3;
    --olive: #7d7b3e;
  }
  * { margin: 0; padding: 0; box-sizing: border-box; }
  html, body {
    width: 1093px;
    height: 1200px;
    overflow: hidden;
    background: var(--page);
    font-family: "Source Sans 3", Arial, sans-serif;
  }
  .canvas { position: relative; width: 1093px; height: 1200px; }

  /* back of card: framed panel */
  .back-frame {
    position: absolute;
    left: 444px; top: 553px;
    width: 649px; height: 647px;
    background: var(--frame);
  }
  .back-card {
    position: absolute;
    left: 486px; top: 611px;
    width: 566px; height: 527px;
    background: var(--card);
  }
  .back-card-tail {
    position: absolute;
    left: 1013px; top: 1138px;
    width: 39px; height: 62px;
    background: var(--card);
  }
  .holder-name {
    position: absolute; left: 29px; top: 37px;
    font-size: 21px; color: var(--ink-slate); letter-spacing: 0.2px;
  }
  .holder-role {
    position: absolute; left: 29px; top: 70px;
    font-size: 15.5px; color: var(--ink-slate);
  }
  .contact-list {
    position: absolute; left: 29px; top: 188px;
    list-style: none;
    font-size: 15.5px; line-height: 27px; color: var(--ink-slate);
  }
  .contact-list .web { margin-left: 14px; }
  .service-line {
    position: absolute; left: 31px; top: 470px;
    font-size: 16px; color: var(--olive); white-space: nowrap;
  }

  /* front of card */
  .front-card {
    position: absolute;
    left: 0; top: 0;
    width: 647px; height: 647px;
    background: var(--card);
    box-shadow: 0 0 0 5px var(--page);
  }
  .brand-square {
    position: absolute; left: 102px; top: 150px;
    width: 160px; height: 160px;
    background: var(--mark-sand);
  }
  .brand-name {
    position: absolute; left: 40px; top: 446px;
    font-size: 40px; color: var(--ink-grey); letter-spacing: 0.3px;
    white-space: nowrap;
  }
  .brand-tagline {
    position: absolute; left: 40px; top: 493px;
    font-size: 30px; color: var(--ink-grey); letter-spacing: 0.3px;
    white-space: nowrap;
  }
</style>
</head>
<body>
<main class="canvas">
  <section class="back-frame"></section>
  <section class="back-card">
    <p class="holder-name">DANIEL HARLOW</p>
    <p class="holder-role">Licensed Strata Manager</p>
    <ul class="contact-list">
      <li>PO BOX 48, MILLBROOK NSW 2031</li>
      <li>12/5-19 FERRIS LANE MILLBROOK NSW 2031</li>
      <li>T: 02 9555 0142</li>
      <li>F: 02 9555 0187</li>
      <li>M: 0400 555 318</li>
      <li>E: hello@harlowproperty.com.au<span class="web">www.harlowproperty.com.au</span></li>
    </ul>
    <p class="service-line">Strata Management &nbsp;| Community Management | Property Management</p>
  </section>
  <div class="back-card-tail"></div>

  <section class="front-card">
    <div class="brand-square"></div>
    <p class="brand-name">HARLOW PROPERTY GROUP</p>
    <p class="brand-tagline">STRATA MANAGEMENT SERVICES</p>
  </section>
</main>
</body>
</html>
```